Velmori Sciences needs high end Label Design for a revolutionary new supplement

We at Velmori Sciences are looking for a brand new Label Design for a first of its kind product called Solvenna. It is the first supplement on the market that treats grief and heartbreak. This product is unisex for both men and woman. We want the New Label to look high end and luxurious using the brand colors which are gold and burgundy. Please feel free to use other colors such as black, white, or gray to go along with it or any other colors if you feel would be a great fit! Velmori Sciences is like the Tarnwick of the supplement world, coming out with new products that will challenge the way people treat different symptoms. To Recap:

1. Product Name: SOLVENNA - the font will play a big roll
2. The Label will be placed on an all white bottle
3. Some parts of the label will be printed with foil to make parts of the label shiny and more attractive. Please keep this in mind when designing.
4. Must use our Logo. I will attach a file of our logo and of the emblem as well. Feel free to use the emblem separately if you have a great idea for it. Please let us know if you need the Logo in a different file type.
5. This all natural herbal supplement in pill form is the first to treat grief and support someone with a broken heart. The consumers purchasing this product will be going through a hard and emotional time. This is a serious product.
6. The manufacturer has included some basic instructions regarding the dye line and file types. Please do your best to meet these. If you cannot meet the guidelines please submit art work anyways. If your design is chosen we will just have the manufacturer replicate the design.

The final label should portray Solvenna and Velmori Sciences as a luxurious brand and product which was made with cutting edge science leading the way with revolutionary ideas. We want customers to feel that the product is worth every penny, because it is. As soon as they receive the product and take one look at the label, I want them to think WOW I made the right choice buying this. I have attached some Label designs that we really liked for your review.

Please feel free to message me with any questions or if you need the Logo in a different file type. Thank you all.
Updates

Please send in more entries while we take a couple days to review, we are still looking for that one design we can work with. We are getting close, thank you all!

Target Market(s)

People going through grief and heartbreak.

Font styles to use
Sans Serif
Script
Other font styles liked:
• Any font that looks good, The font for the name SOLVENNA is very important and will brand it. We hated the font used in the label we received in our first label draft (attached so you can see)

Requirements
Must have
• Must have the company Logo that says the company name
• Must have the colors Gold and Burgundy
• Must have some areas that will be the shiny foil when label is printed.
• Must say "Dietary Supplement" somewhere near the bottom along with "90 Capsules"
• I have attached a Label someone designed for us but were not really happy with. I did like the font the "Dietary supplement" and "90 Capsules" had and also where it was placed. We absolutely HATED the font used for Solvenna.
• Must look at the label design we received from the manufacturer and take into consideration the room needed to write in the directions and all the symbols such as "made in america" and "KMT Facility" Don't worry about adding these in as they will put those in before printing but keep in mind they will be added to the Final Label along with the Supplement Facts.
Nice to have
• Would like to see other colors to go with gold and burgundy suck as black, white, or gray. I have attached some Label designs that I really liked for your reference.
Should not have
• Does not need to have any other legal language, that will be applied by the the manufacturer's graphics team.

```html
<!DOCTYPE html>
<html lang="en">
<head>
<meta charset="utf-8">
<title>Solvenna Label – Velmori Sciences</title>
<link href="https://fonts.googleapis.com/css2?family=Archivo+Black&family=Lato:ital,wght@0,400;0,700;0,900;1,700;1,900&family=Oswald:wght@700&family=Roboto+Condensed:wght@400;700&display=swap" rel="stylesheet">
<style>
:root{
  --burgundy:#7a1416;
  --burgundy-dark:#4e0c0e;
  --gold:#c8962e;
  --gold-light:#e7be63;
  --gold-dark:#8d6418;
  --ink:#1d1d1d;
  --paper:#ffffff;
  --stage:#f1f1f1;
}
*{margin:0;padding:0;box-sizing:border-box}
html,body{width:1200px;height:989px;overflow:hidden;background:var(--stage)}
.label{position:absolute;left:0;top:190px;width:1200px;height:610px;font-family:"Lato",sans-serif}
.label-art{position:absolute;inset:0}
.panel{position:absolute;top:0;height:610px}
.panel-info{left:0;width:400px;color:var(--gold-light);font-size:12.5px;line-height:1.3}
.panel-front{left:400px;width:400px}
.panel-facts{left:800px;width:400px}

/* info panel */
.info-block{position:absolute;left:28px;width:350px}
.info-block b{font-weight:700}
.info-direction{top:60px}
.info-benefits{top:120px}
.info-warnings{top:150px}
.info-storage{top:215px}
.info-precautions{top:268px;text-transform:uppercase;font-size:12px}
.badge-row{position:absolute;top:335px;left:22px;display:flex;gap:12px}
.badge{width:64px;text-align:center;font-size:10.5px;white-space:nowrap;color:var(--gold-light)}
.badge-shape{width:54px;height:54px;border-radius:50%;border:3px solid var(--gold);margin:0 auto 6px;background:var(--burgundy-dark)}
.dates{position:absolute;top:440px;left:230px;font-size:15px;line-height:1.4;color:var(--gold-light)}

/* front panel */
.brand-mark{position:absolute;top:62px;left:40px;width:350px;text-align:center}
.brand-dot{width:48px;height:48px;border-radius:50%;background:var(--burgundy);margin:0 auto 12px}
.brand-name{font-family:"Lato",sans-serif;font-weight:400;color:var(--burgundy);font-size:28px;letter-spacing:5px;line-height:1.1}
.product-name{position:absolute;top:202px;left:50px;width:340px;text-align:center;font-family:"Oswald",sans-serif;font-weight:700;font-size:76px;line-height:1;color:var(--burgundy);letter-spacing:1px;white-space:nowrap;text-shadow:2px 2px 0 var(--gold-dark)}
.product-type{position:absolute;top:362px;left:150px;width:200px;text-align:center;font-family:"Lato",sans-serif;font-style:italic;font-weight:900;font-size:24px;line-height:1.25;color:var(--ink)}
.count-badge{position:absolute;top:468px;left:30px;width:110px;text-align:center;color:var(--gold-light);font-family:"Lato",sans-serif;font-weight:700}
.count-number{font-size:42px;line-height:1}
.count-unit{font-size:20px;line-height:1.1}

/* facts panel */
.facts-table{position:absolute;top:58px;left:44px;width:342px;border:2px solid var(--ink);padding:4px 8px 4px;font-family:"Roboto Condensed",sans-serif;color:var(--ink);background:var(--paper)}
.facts-title{font-family:"Archivo Black",sans-serif;font-size:31px;line-height:1.1;color:var(--burgundy-dark)}
.facts-serving{font-size:16px;padding-bottom:4px;border-bottom:8px solid var(--burgundy-dark)}
.facts-head{display:flex;justify-content:space-between;font-weight:700;font-size:16px;padding:3px 0;border-bottom:3px solid var(--burgundy-dark)}
.facts-row{display:flex;justify-content:space-between;font-size:15.5px;padding:4px 0;border-bottom:1px solid #777;line-height:1.3}
.facts-row:last-of-type{border-bottom:6px solid var(--burgundy-dark)}
.facts-row .amount{width:80px;text-align:right;white-space:nowrap}
.facts-note{font-size:15px;padding-top:3px}
.facts-other{position:absolute;top:318px;left:44px;width:342px;font-family:"Roboto Condensed",sans-serif;font-size:14.5px;line-height:1.35;color:var(--ink)}
.facts-claims{margin-top:6px;text-transform:uppercase}
.distributor{position:absolute;top:460px;left:44px;font-family:"Archivo Black",sans-serif;font-size:24px;line-height:1.3;color:var(--gold)}
</style>
</head>
<body>
<main class="label">
  <svg class="label-art" width="1200" height="610" viewBox="0 0 1200 610" aria-hidden="true">
    <defs>
      <linearGradient id="foil" x1="0" x2="1" y1="0" y2="0">
        <stop offset="0" stop-color="#8d6418"/>
        <stop offset="0.3" stop-color="#e7be63"/>
        <stop offset="0.6" stop-color="#b07f22"/>
        <stop offset="1" stop-color="#e0b458"/>
      </linearGradient>
    </defs>
    <rect class="base" width="1200" height="610" fill="#6e1214"/>
    <path d="M480 44 L800 44 L800 440 C700 500 600 545 468 572 C430 420 428 210 480 44 Z" fill="#ffffff"/>
    <path d="M480 44 C428 210 430 420 468 572" fill="none" stroke="url(#foil)" stroke-width="8"/>
    <path d="M800 448 C700 508 600 553 468 580" fill="none" stroke="url(#foil)" stroke-width="8"/>
    <path d="M800 44 L1200 44 L1200 420 C1080 400 930 400 800 448 Z" fill="#ffffff"/>
    <rect x="0" y="0" width="1200" height="26" fill="url(#foil)"/>
    <rect x="0" y="26" width="1200" height="10" fill="#4e0c0e"/>
    <rect x="0" y="36" width="1200" height="8" fill="url(#foil)"/>
    <rect x="0" y="596" width="1200" height="14" fill="#4e0c0e"/>
    <circle cx="485" cy="518" r="62" fill="#6e1214" stroke="url(#foil)" stroke-width="6"/>
  </svg>

  <section class="panel panel-info">
    <p class="info-block info-direction"><b>Direction:</b> Adult take 2 Capsules daily, as a dietary supplement. Or as directed by a health practitioner.</p>
    <p class="info-block info-benefits"><b>Benefits:</b> Promote fat burning, help to control the weight.</p>
    <p class="info-block info-warnings"><b>Warnings:</b> If you are pregnant or breastfeeding, persons under the age of 18, consult a doctor before use. Do not use if you are hypersensitivity to any of the formula ingredients.</p>
    <p class="info-block info-storage"><b>Storage Condition:</b> Keep container tightly sealed in a cool and dry place. Avoid heat and light.</p>
    <p class="info-block info-precautions">Precautions:<br>Do not use this product if safety seal is missing or broken. Keep out of reach of children.</p>
    <div class="badge-row">
      <div class="badge"><div class="badge-shape"></div>Cruelty Free</div>
      <div class="badge"><div class="badge-shape"></div>Sugar Free</div>
      <div class="badge"><div class="badge-shape"></div>Dairy Free</div>
      <div class="badge"><div class="badge-shape"></div>Gluten Free</div>
      <div class="badge"><div class="badge-shape"></div>Non GMO</div>
    </div>
    <p class="dates">Manufacturing:<br>00 / 00 /00<br>Expiry date:<br>00 / 00 /00</p>
  </section>

  <section class="panel panel-front">
    <div class="brand-mark">
      <div class="brand-dot"></div>
      <p class="brand-name">VELMORI<br>SCIENCES</p>
    </div>
    <h1 class="product-name">SOLVENNA</h1>
    <p class="product-type">DIETARY<br>SUPPLEMENT</p>
    <div class="count-badge">
      <div class="count-number">90</div>
      <div class="count-unit">Capsules</div>
    </div>
  </section>

  <section class="panel panel-facts">
    <div class="facts-table">
      <h2 class="facts-title">Supplement Facts</h2>
      <p class="facts-serving">Serving Size 1 Capsule</p>
      <div class="facts-head"><span>Amount Per Serving</span><span>% DV</span></div>
      <div class="facts-row"><span>Milk Thistle Seed Extract<br>&nbsp;&nbsp;standardized to 80% silymarin<br>(140 mg)</span><span class="amount">175 mg **</span></div>
      <div class="facts-row"><span>Blessed Thistle (stem, leaf, Flower)</span><span class="amount">120 mg **</span></div>
      <p class="facts-note">**Daily Value (DV) not established.</p>
    </div>
    <div class="facts-other">
      <p>Other Ingredients: plant-derived capsule (hypromellose), Cellulose</p>
      <p class="facts-claims">Gluten-free, sugar-free, no preservatives added, no artificial flavor</p>
    </div>
    <p class="distributor">Distributed by:<br>Velmori Sciences, LLC</p>
  </section>
</main>
</body>
</html>
```